Irrigation Business needs their business cards modernised and revamped

I would like to keep my current logo, colours and revamp the format of the card.

I would like the card to be clean yet important.

Im not sure if you include texture but i would like the named logo to be indented into the card etc.

show me something alive and free something thats clinical to the point yet has a feel of achievement. i would like people to go nice card.

Target Market(s)

high end clients, corporate, sports field manger, the guys that make the decisions

Industry/Entity Type

Business

Contact Information for Business Card

nformation to be included

Dean Harlow (Director)
0487305526
dean@kolvat.biz
www.kestonfieldworks.com

instagram logo
google logo
facebook logo

Colors

Designer to choose colors to be used in the design.

Requirements
Nice to have
• indentations a really nice feel to the card good texture

```html
<!DOCTYPE html>
<html lang="en">
<head>
<meta charset="utf-8">
<title>Keston Fieldworks – Business Card</title>
<link rel="stylesheet" href="https://fonts.googleapis.com/css2?family=Open+Sans:wght@400;600;700;800&display=swap">
<style>
  :root {
    --page-bg: #2b2b2d;
    --green-light: #52de9f;
    --green-dark: #2e9e62;
    --green-text: #3cb56e;
    --blue: #2f6db5;
    --blue-bright: #2c9ad8;
    --blue-pale: #6cc0ec;
    --card-white: #f6f6f4;
    --ink: #555a60;
    --rule: #c9cacc;
    --white: #ffffff;
  }
  * { box-sizing: border-box; margin: 0; padding: 0; }
  html, body {
    width: 1200px; height: 840px; overflow: hidden;
    background: var(--page-bg);
    font-family: "Open Sans", Arial, sans-serif;
  }
  .canvas {
    position: relative; width: 1200px; height: 840px;
    display: flex; align-items: center; justify-content: center; gap: 40px;
  }
  .card {
    position: relative; width: 540px; height: 310px; overflow: hidden;
    box-shadow: 0 14px 30px rgba(0,0,0,0.45);
  }

  /* Back of card */
  .card-back {
    background: linear-gradient(100deg, var(--green-light) 0%, var(--green-dark) 100%);
    display: flex; flex-direction: column; align-items: center; justify-content: center;
  }
  .back-brand {
    display: flex; align-items: center; gap: 14px; margin-top: 10px;
  }
  .back-brand .mark {
    width: 58px; height: 58px; border-radius: 50%;
    border: 4px solid var(--white);
  }
  .back-brand .name {
    color: var(--white); font-weight: 700; font-size: 22px; letter-spacing: 1px;
  }
  .social-row {
    display: flex; gap: 8px; margin-top: 54px;
  }
  .social-row .dot {
    width: 16px; height: 16px; border-radius: 50%;
    border: 1.5px solid var(--white);
  }

  /* Front of card */
  .card-front { background: var(--card-white); }
  .front-brand {
    position: absolute; left: 34px; top: 106px; width: 200px;
    display: flex; flex-direction: column; align-items: center; gap: 10px;
  }
  .front-brand .mark {
    width: 54px; height: 54px; border-radius: 50%; background: var(--blue-bright);
  }
  .front-brand .name {
    color: var(--blue); font-weight: 800; font-size: 19px; text-align: center; line-height: 1.15;
  }
  .divider {
    position: absolute; left: 262px; top: 58px; width: 1px; height: 122px;
    background: var(--rule);
  }
  .contact {
    position: absolute; left: 282px; top: 60px;
  }
  .contact .person { color: var(--blue); font-weight: 700; font-size: 14px; letter-spacing: 0.2px; }
  .contact .role { color: var(--green-text); font-size: 14px; margin-bottom: 10px; }
  .contact ul { list-style: none; }
  .contact li {
    display: flex; align-items: center; gap: 8px;
    color: var(--ink); font-size: 12px; line-height: 19px;
  }
  .contact svg { width: 11px; height: 11px; fill: var(--blue); flex: none; }
  .corner-mark {
    position: absolute; right: 20px; bottom: 28px;
    width: 30px; height: 30px; border-radius: 50%; background: var(--blue-bright);
  }
  .stripes {
    position: absolute; left: 0; right: 0; bottom: 0; height: 24px;
    background: repeating-linear-gradient(to bottom,
      var(--blue-bright) 0 4px, var(--blue-pale) 4px 5px);
  }
</style>
</head>
<body>
<main class="canvas">
  <section class="card card-back" aria-label="Card back">
    <div class="back-brand">
      <span class="mark"></span>
      <span class="name">KESTON FIELDWORKS</span>
    </div>
    <div class="social-row" aria-label="Social profiles">
      <span class="dot"></span><span class="dot"></span><span class="dot"></span>
    </div>
  </section>

  <section class="card card-front" aria-label="Card front">
    <div class="front-brand">
      <span class="mark"></span>
      <span class="name">KESTON FIELDWORKS</span>
    </div>
    <div class="divider"></div>
    <div class="contact">
      <p class="person">DEAN HARLOW</p>
      <p class="role">DIRECTOR</p>
      <ul>
        <li>
          <svg viewBox="0 0 24 24"><path d="M6.6 10.8a15 15 0 0 0 6.6 6.6l2.2-2.2a1 1 0 0 1 1-.25 11.4 11.4 0 0 0 3.6.57 1 1 0 0 1 1 1V20a1 1 0 0 1-1 1A17 17 0 0 1 3 4a1 1 0 0 1 1-1h3.5a1 1 0 0 1 1 1c0 1.25.2 2.45.57 3.57a1 1 0 0 1-.25 1z"/></svg>
          0487305526
        </li>
        <li>
          <svg viewBox="0 0 24 24"><path d="M2 5h20v14H2z M2 5l10 8 10-8" /></svg>
          dean@kolvat.biz
        </li>
        <li>
          <svg viewBox="0 0 24 24"><circle cx="12" cy="12" r="10"/></svg>
          www.kestonfieldworks.com
        </li>
      </ul>
    </div>
    <span class="corner-mark"></span>
    <div class="stripes"></div>
  </section>
</main>
</body>
</html>
```